Business card for a new innovative and professional lawn care business

We need a business card design for a new lawn care business in Halifax NS Canada. We offer lawn services in Halifax & Bedford. Our services offered include lawn care, garden services, and property maintenance. We take pride in our work and are experienced at what we do. I would like to see a design that is double sided. On the backside I would like the something simple (maybe my logo preferably on blackround (linked below) with website link, Facebook page or something). The front I want to include contact info:
Morgan Pell
phone 902-555-0148
email - brookvaleyards.ca
facebook - Facebook.com/brookvaleyards
Instagram maybe ? - instagram.com/brookvaleyard
Serving Halifax and Bedford for 5 years?
I don't want it to have too much information as I will be passing them out in aim to visit website, or call !
We do want it to include lawn care, garden services and property maintenance.
Basic, catchy, and modern looking !
Logo attached below !

Target Market(s)

Passing business cards to everyone I meet or interact with.

Industry/Entity Type

Lawn Care

Contact Information for Business Card

Double sided with some basic information, with catchy colours and easy to look at.

Font styles to use
Sans Serif

Requirements
Must have
• Must be double sided and have :
• Name, Phone, Email, FB, Website, and 3 main services offered - lawn care, property maintenance, garden services
Nice to have
• Would be nice to have instagram link if it goes well on there
Should not have
• Don't want too much writing or images that are distracting

```html
<!DOCTYPE html>
<html lang="en">
<head>
<meta charset="utf-8">
<title>Brookvale Yards – Business Card</title>
<link rel="stylesheet" href="https://fonts.googleapis.com/css2?family=Open+Sans:wght@400;600;700&display=swap">
<style>
  :root {
    --green-dark: #1f7a3a;
    --green-mid: #2f8f3f;
    --green-light: #8cc63f;
    --ink: #3a3a3a;
    --paper: #ffffff;
    --backdrop: #e9ebe6;
    --rule: #d6d6d6;
  }
  * { box-sizing: border-box; margin: 0; padding: 0; }
  html, body { width: 1200px; height: 950px; overflow: hidden; }
  body {
    background: var(--backdrop);
    font-family: "Open Sans", Arial, sans-serif;
    color: var(--ink);
    position: relative;
  }
  .card {
    position: absolute;
    left: 250px;
    width: 700px;
    height: 400px;
    background: var(--paper);
    box-shadow: 0 6px 18px rgba(0,0,0,0.15);
    overflow: hidden;
  }
  .card--front { top: 50px; }
  .card--back { top: 500px; }

  .swoosh { position: absolute; left: 0; bottom: 0; width: 700px; height: 400px; }

  .brand {
    position: absolute;
    left: 50px;
    top: 150px;
    width: 270px;
    display: flex;
    align-items: center;
    gap: 12px;
  }
  .brand__dot {
    width: 22px; height: 22px; border-radius: 50%;
    background: var(--green-light);
    flex: none;
  }
  .brand__name {
    font-weight: 700;
    font-size: 34px;
    line-height: 1.05;
    color: var(--green-mid);
    text-transform: uppercase;
    letter-spacing: 1px;
  }

  .divider {
    position: absolute;
    left: 345px; top: 40px;
    width: 1px; height: 215px;
    background: var(--rule);
  }

  .contact {
    position: absolute;
    left: 380px; top: 48px;
  }
  .contact__name {
    font-weight: 700;
    font-size: 26px;
    color: var(--green-mid);
    margin-bottom: 12px;
  }
  .contact__list { list-style: none; }
  .contact__item {
    display: flex; align-items: center; gap: 10px;
    font-size: 16px; line-height: 28px;
  }
  .contact__icon { width: 16px; height: 16px; flex: none; }
  .contact__badge {
    width: 15px; height: 15px; flex: none;
    background: var(--ink); border-radius: 2px;
  }

  .mower-art {
    position: absolute;
    left: 190px; top: 50px;
    width: 320px; height: 220px;
    background: radial-gradient(ellipse at center, #2e8a45 0%, #1f7a3a 55%, #e7f1e9 100%);
    border-radius: 6px;
  }
  .services {
    position: absolute;
    left: 0; right: 0; top: 310px;
    display: flex; justify-content: center; gap: 30px;
    list-style: none;
  }
  .services__item {
    display: flex; align-items: center; gap: 8px;
    font-size: 20px; color: var(--ink);
    white-space: nowrap;
  }
  .services__tick { width: 18px; height: 18px; flex: none; }
</style>
</head>
<body>

<section class="card card--front" aria-label="Business card front">
  <svg class="swoosh" viewBox="0 0 700 400" aria-hidden="true">
    <path d="M0,330 C250,395 460,300 700,220 L700,400 L0,400 Z" fill="var(--green-dark)"/>
    <path d="M0,346 C255,405 465,318 700,240 L700,400 L0,400 Z" fill="var(--paper)"/>
    <path d="M0,354 C260,410 470,328 700,252 L700,400 L0,400 Z" fill="var(--green-light)"/>
    <path d="M0,385 C280,420 500,370 700,330 L700,400 L0,400 Z" fill="var(--green-mid)" opacity="0.55"/>
  </svg>

  <div class="brand">
    <span class="brand__dot"></span>
    <span class="brand__name">Brookvale<br>Yards</span>
  </div>

  <div class="divider"></div>

  <div class="contact">
    <h1 class="contact__name">Morgan Pell</h1>
    <ul class="contact__list">
      <li class="contact__item">
        <svg class="contact__icon" viewBox="0 0 24 24" aria-hidden="true"><path fill="var(--ink)" d="M6.6 10.8a15 15 0 0 0 6.6 6.6l2.2-2.2a1 1 0 0 1 1-.25 11.4 11.4 0 0 0 3.6.57 1 1 0 0 1 1 1V20a1 1 0 0 1-1 1A17 17 0 0 1 3 4a1 1 0 0 1 1-1h3.5a1 1 0 0 1 1 1c0 1.25.2 2.45.57 3.6a1 1 0 0 1-.25 1z"/></svg>
        902-555-0148
      </li>
      <li class="contact__item">
        <svg class="contact__icon" viewBox="0 0 24 24" aria-hidden="true"><rect x="2" y="5" width="20" height="14" rx="2" fill="var(--ink)"/><path d="M3 6l9 7 9-7" stroke="#fff" stroke-width="2" fill="none"/></svg>
        info@brookvaleyards.ca
      </li>
      <li class="contact__item"><span class="contact__badge"></span>brookvaleyards.ca</li>
      <li class="contact__item"><span class="contact__badge"></span>brookvaleyards</li>
      <li class="contact__item"><span class="contact__badge"></span>brookvaleyard</li>
    </ul>
  </div>
</section>

<section class="card card--back" aria-label="Business card back">
  <div class="mower-art" role="img" aria-label="Green illustration of a push lawn mower"></div>
  <ul class="services">
    <li class="services__item">
      <svg class="services__tick" viewBox="0 0 24 24" aria-hidden="true"><path d="M3 13l6 6L21 5" stroke="var(--green-light)" stroke-width="4" fill="none" stroke-linecap="round" stroke-linejoin="round"/></svg>
      Lawn Care
    </li>
    <li class="services__item">
      <svg class="services__tick" viewBox="0 0 24 24" aria-hidden="true"><path d="M3 13l6 6L21 5" stroke="var(--green-light)" stroke-width="4" fill="none" stroke-linecap="round" stroke-linejoin="round"/></svg>
      Property Maintenance
    </li>
    <li class="services__item">
      <svg class="services__tick" viewBox="0 0 24 24" aria-hidden="true"><path d="M3 13l6 6L21 5" stroke="var(--green-light)" stroke-width="4" fill="none" stroke-linecap="round" stroke-linejoin="round"/></svg>
      Garden Services
    </li>
  </ul>
</section>

</body>
</html>
```